Website Design For Tessel Hub Project

www.tesselhub.com.au

As the name suggests i would like to have a design for this website... the website is nothing to do with night life or parties, but it is do everything to do with being online all the time, being available 24/7.

all information needed regarding anything to do with this City and its businesses. so, Basically This will be an online business directory for local businesses. What i am looking for is a website that can display Business listings in a pleasant, lively, friendly, attitude that reflects the towns people, this city boasts with a largest inland city in Australia, and a local university to match, it has its own airport, malls, markets and supermarkets. This website directory/each business layout will be very similar to the ones on www.marlowgate-web.com.au.

Wagga Wagga has a community of numerous backgrounds, cutlures, creeds and beliefs and religions to be a thriving one.

Therefore, i want the website to reflect its green hills and flowing rivers. The is a advertising point.

An online venue for the local and surrounding bussinesses to be found with a minimum amount of clicks and hassles. Essentially it is a business directory, but not just any directory you see online. I do not want it to look like the quarry lists or dune ledger. this website directory is specific to one location and its bussinesses are particular to that area. I want the website to almost have an emotion for that City, not just an army of black and white ants marching across the page.

Yours colours are you own imagination as long as it is visible and readable by majority of people; its colours are pleasant and not offensive to the eyes: i.e: not too bright, not too dark and depressing.

"tesselhub" is to be included in your website design.
Updates

Reason: The deadline has been extended as there are few nice concepts however they need to be a bit more clean in its layout, the color choices are not quite right, as well as the banners need to look more presentable. Thanks

Target Market(s)

The Target Market is Small to Medum Businesses to List their business online and Gen Y and Mums & dads looking for services in the city of Wagga Wagga

Industry/Entity Type

Business Directory

Requirements
Must have
• Search Bar
Social Media Widgets (LoopNest, Vexora, Pebble twine)
Categories
Sliding Banners
Each Major Category Should have an image or a nice Icon representing the category

```html
<!DOCTYPE html>
<html lang="en">
<head>
<meta charset="utf-8">
<title>Tessel Hub – Local Business Directory</title>
<link rel="stylesheet" href="https://fonts.googleapis.com/css2?family=Arimo:wght@400;700&family=Open+Sans:wght@300;400&family=PT+Sans+Narrow&display=swap">
<style>
:root{
  --blue:#1a77b5;
  --blue-dark:#12517f;
  --blue-band:#1f5f8f;
  --footer:#2a6a99;
  --link:#1f7ab8;
  --text:#333;
  --muted:#666;
  --rule:#d6d6d6;
  --head-dark:#1b1b1b;
  --star:#f2c232;
  --star-edge:#c9952a;
  --white:#fff;
}
*{box-sizing:border-box;margin:0;padding:0}
html,body{width:667px;height:1200px;overflow:hidden;background:var(--white)}
body{font-family:"Arimo",Arial,sans-serif;color:var(--text);position:relative}
.page{position:relative;width:667px;height:1200px;overflow:hidden}
a{color:inherit;text-decoration:none}

/* header */
.brand{position:absolute;left:22px;top:52px;display:flex;align-items:center;gap:8px;
  font-weight:700;font-size:26px;color:var(--blue)}
.brand-dot{width:22px;height:22px;border-radius:50%;background:var(--blue)}
.search{position:absolute;left:336px;top:38px;width:309px;height:34px;border-radius:6px;
  background:linear-gradient(#3a3a3a,#111);padding:5px 6px;display:flex;align-items:center;gap:4px}
.search-field{flex:1;height:22px;border-radius:3px;background:var(--white);border:1px solid #999;
  font-size:10px;color:#222;line-height:20px;padding-left:6px}
.search-btn{width:24px;height:24px;display:flex;align-items:center;justify-content:center}
.nav-shape{position:absolute;left:0;top:97px}
.nav{position:absolute;left:170px;top:101px;height:32px;display:flex;list-style:none}
.nav li{height:32px;line-height:32px;font-size:11.5px;color:var(--white);text-align:center;
  border-left:1px solid rgba(255,255,255,.18);border-right:1px solid rgba(0,0,0,.15)}
.nav li:first-child{border-left:none}

/* banner */
.slider{position:absolute;left:20px;top:141px;width:626px;height:186px;border:1px solid #cfcfcf;border-radius:4px;
  background:linear-gradient(#f7f7f7,#dedede)}
.slide-art{position:absolute;left:15px;top:4px;width:285px;height:176px;border-radius:4px;
  background:radial-gradient(ellipse at 55% 55%,#bfe0f6 0%,#7fb9e4 45%,rgba(220,220,220,0) 75%)}
.slide-copy{position:absolute;left:308px;top:18px;width:292px;text-align:center}
.slide-title{font-family:"Open Sans",Arial,sans-serif;font-weight:300;font-size:17px;color:var(--link);white-space:nowrap}
.slide-text{margin-top:11px;font-size:9.2px;line-height:16.5px;color:#777}
.btn-more{position:absolute;left:411px;top:133px;width:86px;height:22px;line-height:20px;border-radius:3px;text-align:center;
  background:linear-gradient(#2d8fd0,#166aa6);border:1px solid #0f5588;color:var(--white);font-size:10.5px}
.arrow{position:absolute;top:79px;width:21px;height:21px;border-radius:50%;background:var(--white);border:1px solid #bbb;
  display:flex;align-items:center;justify-content:center}
.arrow.prev{left:6px}.arrow.next{right:9px}

/* sidebar */
.sidebox{position:absolute;left:22px;width:169px;border:1px solid #d2d2d2;
  background:linear-gradient(90deg,#e6e6e6,#f8f8f8 45%,#f8f8f8 55%,#e6e6e6)}
.sidebox h2{height:36px;line-height:36px;padding-left:15px;font-family:"PT Sans Narrow",Arial,sans-serif;font-weight:400;
  font-size:19.5px;color:var(--white);background:linear-gradient(#555 0%,var(--head-dark) 55%,#2a2a2a 100%)}
.sidebox ul{list-style:none;padding:8px 0 0 18px}
.sidebox li{height:20px;line-height:12px;font-size:9.6px;color:#444;position:relative;padding-left:18px}
.sidebox li::before{content:"";position:absolute;left:0;top:1px;width:9px;height:9px;border-radius:50%;
  background:linear-gradient(#fff,#ccc);border:1px solid #aaa}
.sidebox li::after{content:"";position:absolute;left:4px;top:4px;border-left:3px solid #555;border-top:2px solid transparent;border-bottom:2px solid transparent}

/* main */
.alpha{position:absolute;left:207px;top:343px;width:438px;height:28px;background:var(--blue-band);
  display:flex;justify-content:space-between;align-items:center;padding:0 10px 0 12px;
  font-family:"Arimo",Arial,sans-serif;font-size:11px;color:var(--white)}
.section-title{position:absolute;left:211px;width:430px;font-family:"PT Sans Narrow",Arial,sans-serif;font-weight:400;
  font-size:20px;color:#222;border-bottom:1px solid var(--rule);padding-bottom:2px}
.popular{position:absolute;left:211px;top:430px;width:434px;display:grid;grid-template-columns:236px 198px}
.popular .cat{font-size:9.4px;line-height:16px;height:48px}
.popular .cat h3{font-weight:400;font-size:9.4px;color:var(--link)}
.popular .cat p{color:#444}
.results{position:absolute;left:211px;top:612px;width:430px;text-align:right;font-size:10.5px;color:var(--muted)}
.listing{position:absolute;left:210px;width:433px;height:119px;border:1px solid #dcdcdc;border-radius:4px;
  background:linear-gradient(#fff,#fbfbfb);box-shadow:0 1px 2px rgba(0,0,0,.08);padding:10px 12px}
.listing h3{font-weight:400;font-size:11px;color:var(--link);line-height:14px}
.listing p{font-size:9.2px;line-height:11.5px;color:#444;margin-top:9.5px;width:400px}
.listing p:first-of-type{margin-top:10px}
.stars{position:absolute;right:8px;top:4px;display:flex;gap:1px}

/* footer */
.footer{position:absolute;left:0;top:1113px;width:667px;height:87px;background:var(--footer);color:var(--white)}
.social{position:absolute;left:30px;top:37px;display:flex;gap:5px}
.social span{width:18px;height:18px;border-radius:2px;background:#dbe8f2;border:1px solid #9fc0da}
.footer-links{position:absolute;right:22px;top:26px;font-size:9.4px;text-align:right;line-height:16px}
</style>
</head>
<body>
<div class="page">

  <header>
    <a class="brand" href="#"><span class="brand-dot"></span>Tessel Hub</a>

    <form class="search" role="search">
      <div class="search-field">search...</div>
      <div class="search-btn">
        <svg width="18" height="18" viewBox="0 0 18 18" aria-hidden="true"><circle cx="7.5" cy="7.5" r="5" fill="none" stroke="#fff" stroke-width="2.4"/><line x1="11" y1="11" x2="16" y2="16" stroke="#fff" stroke-width="3" stroke-linecap="round"/></svg>
      </div>
    </form>

    <svg class="nav-shape" width="667" height="40" viewBox="0 0 667 40" aria-hidden="true">
      <defs><linearGradient id="navFill" x1="0" y1="0" x2="0" y2="1"><stop offset="0" stop-color="#3aa2e0"/><stop offset="1" stop-color="#1468a6"/></linearGradient></defs>
      <path d="M20 33 H155 C168 33 166 4 185 4 H646 V36 H20 Z" fill="url(#navFill)"/>
      <path d="M20 33 H155 C168 33 166 4 185 4" fill="none" stroke="#0f5588" stroke-width="1"/>
    </svg>
    <ul class="nav">
      <li style="width:72px">Home</li>
      <li style="width:76px">About Us</li>
      <li style="width:75px">Gallery</li>
      <li style="width:124px">Tessel Hub Online</li>
      <li style="width:129px">Advanced Search</li>
    </ul>
  </header>

  <section class="slider">
    <div class="slide-art" role="img" aria-label="Folded world map with a red location pin"></div>
    <div class="slide-copy">
      <h1 class="slide-title">LOREM IPSUM DOLOR SIT AMET</h1>
      <p class="slide-text">Lorem ipsum dolor sit amet, consectetur adipisicing elit, sed do eiusmod tempor incididunt ut labore et dolore magna aliqua. Ut enim ad minim veniam, quis nostrud exercitation ullamco laboris nisi ut aliquip ex ea commodo consequat...</p>
    </div>
    <a class="btn-more" href="#">Learn more..</a>
    <span class="arrow prev"><svg width="8" height="10" viewBox="0 0 8 10" aria-hidden="true"><path d="M6 1 L2 5 L6 9" fill="none" stroke="#222" stroke-width="1.8"/></svg></span>
    <span class="arrow next"><svg width="8" height="10" viewBox="0 0 8 10" aria-hidden="true"><path d="M2 1 L6 5 L2 9" fill="none" stroke="#222" stroke-width="1.8"/></svg></span>
  </section>

  <aside>
    <div class="sidebox" style="top:343px;height:167px">
      <h2>Categories</h2>
      <ul><li>Auto/Trade (2)</li><li>Beauty (1)</li><li>Entertainment (0)</li><li>Food &amp; Wine (16)</li><li>Professional Services (15)</li><li>Retail (0)</li></ul>
    </div>
    <div class="sidebox" style="top:517px;height:168px">
      <h2>Recently Added</h2>
      <ul><li>Brightleaf Book Services</li><li>Pastello Cafe</li><li>Norbury Elite Dental</li><li>Brightleaf Book Services</li><li>Pastello Cafe</li><li>Norbury Elite Dental</li></ul>
    </div>
    <div class="sidebox" style="top:692px;height:167px">
      <h2>Recently Updated</h2>
      <ul><li>Brightleaf Book Services</li><li>Pastello Cafe</li><li>Norbury Elite Dental</li><li>Brightleaf Book Services</li><li>Pastello Cafe</li><li>Norbury Elite Dental</li></ul>
    </div>
    <div class="sidebox" style="top:866px;height:167px">
      <h2>Featured Listings</h2>
      <ul><li>Brightleaf Book Services</li><li>Pastello Cafe</li><li>Norbury Elite Dental</li><li>Brightleaf Book Services</li><li>Pastello Cafe</li><li>Norbury Elite Dental</li></ul>
    </div>
  </aside>

  <main>
    <nav class="alpha"><span>0-9</span><span>A</span><span>B</span><span>C</span><span>D</span><span>E</span><span>F</span><span>G</span><span>H</span><span>I</span><span>J</span><span>K</span><span>L</span><span>M</span><span>N</span><span>O</span><span>P</span><span>Q</span><span>R</span><span>S</span><span>T</span><span>U</span><span>V</span><span>W</span><span>X</span><span>Y</span><span>Z</span></nav>

    <h2 class="section-title" style="top:392px">Popular Business Searches</h2>
    <div class="popular">
      <div class="cat"><h3>Auto/Trade</h3><p>Auto Electricians, Auto Retails, Bikes, Body Repair...</p></div>
      <div class="cat"><h3>Food &amp; Wine</h3><p>Baker, Bar, Bottleshop, Butcher...</p></div>
      <div class="cat"><h3>Beauty</h3><p>Beauty Suppliers, Day Spa, Hair, Massage...</p></div>
      <div class="cat" style="height:64px"><h3>Professional Services</h3><p>Accountants, Advertising Agencies, Alternative Therapies, Architect...</p></div>
      <div class="cat" style="margin-top:-16px"><h3>Entertainment</h3><p>Cinema, Gallery, Theater, Video</p></div>
      <div class="cat"><h3>Retail</h3><p>Accessories, Art &amp; Craft, Books, Electical...</p></div>
    </div>

    <h2 class="section-title" style="top:585px">Listings</h2>
    <div class="results">Results 1 - 9 of 9</div>

    <article class="listing" style="top:632px">
      <h3>Pastello Cafe</h3>
      <div class="stars" aria-label="4 stars"><svg width="58" height="14" viewBox="0 0 58 14" aria-hidden="true"><g fill="var(--star)" stroke="var(--star-edge)" stroke-width=".6"><polygon points="7,1 8.8,5 13,5.3 9.8,8.1 10.8,12.5 7,10.2 3.2,12.5 4.2,8.1 1,5.3 5.2,5"/><polygon transform="translate(14.5 0)" points="7,1 8.8,5 13,5.3 9.8,8.1 10.8,12.5 7,10.2 3.2,12.5 4.2,8.1 1,5.3 5.2,5"/><polygon transform="translate(29 0)" points="7,1 8.8,5 13,5.3 9.8,8.1 10.8,12.5 7,10.2 3.2,12.5 4.2,8.1 1,5.3 5.2,5"/><polygon transform="translate(43.5 0)" points="7,1 8.8,5 13,5.3 9.8,8.1 10.8,12.5 7,10.2 3.2,12.5 4.2,8.1 1,5.3 5.2,5"/></g></svg></div>
      <p>All of our Pastizzi's and Pastas are home made right here on the premises.</p>
      <p>Our coffee's are created by our Baristas and we only use the best 'Primo Tazza' 100 % Arabica blend coffee Beans.</p>
      <p>We are open from early (9ish) to late (someti ...</p>
    </article>

    <article class="listing" style="top:758px">
      <h3>Kestrel Legal Lawyers &amp; Solicitors</h3>
      <div class="stars" aria-label="4 stars"><svg width="58" height="14" viewBox="0 0 58 14" aria-hidden="true"><g fill="var(--star)" stroke="var(--star-edge)" stroke-width=".6"><polygon points="7,1 8.8,5 13,5.3 9.8,8.1 10.8,12.5 7,10.2 3.2,12.5 4.2,8.1 1,5.3 5.2,5"/><polygon transform="translate(14.5 0)" points="7,1 8.8,5 13,5.3 9.8,8.1 10.8,12.5 7,10.2 3.2,12.5 4.2,8.1 1,5.3 5.2,5"/><polygon transform="translate(29 0)" points="7,1 8.8,5 13,5.3 9.8,8.1 10.8,12.5 7,10.2 3.2,12.5 4.2,8.1 1,5.3 5.2,5"/><polygon transform="translate(43.5 0)" points="7,1 8.8,5 13,5.3 9.8,8.1 10.8,12.5 7,10.2 3.2,12.5 4.2,8.1 1,5.3 5.2,5"/></g></svg></div>
      <p>All of our Pastizzi's and Pastas are home made right here on the premises.</p>
      <p>Our coffee's are created by our Baristas and we only use the best 'Primo Tazza' 100 % Arabica blend coffee Beans.</p>
      <p>We are open from early (9ish) to late (someti ...</p>
    </article>

    <article class="listing" style="top:884px">
      <h3>Savanna Table Restaurant</h3>
      <div class="stars" aria-label="4 stars"><svg width="58" height="14" viewBox="0 0 58 14" aria-hidden="true"><g fill="var(--star)" stroke="var(--star-edge)" stroke-width=".6"><polygon points="7,1 8.8,5 13,5.3 9.8,8.1 10.8,12.5 7,10.2 3.2,12.5 4.2,8.1 1,5.3 5.2,5"/><polygon transform="translate(14.5 0)" points="7,1 8.8,5 13,5.3 9.8,8.1 10.8,12.5 7,10.2 3.2,12.5 4.2,8.1 1,5.3 5.2,5"/><polygon transform="translate(29 0)" points="7,1 8.8,5 13,5.3 9.8,8.1 10.8,12.5 7,10.2 3.2,12.5 4.2,8.1 1,5.3 5.2,5"/><polygon transform="translate(43.5 0)" points="7,1 8.8,5 13,5.3 9.8,8.1 10.8,12.5 7,10.2 3.2,12.5 4.2,8.1 1,5.3 5.2,5"/></g></svg></div>
      <p>All of our Pastizzi's and Pastas are home made right here on the premises.</p>
      <p>Our coffee's are created by our Baristas and we only use the best 'Primo Tazza' 100 % Arabica blend coffee Beans.</p>
      <p>We are open from early (9ish) to late (someti ...</p>
    </article>
  </main>

  <footer class="footer">
    <div class="social">
      <span role="img" aria-label="LoopNest"></span>
      <span role="img" aria-label="Vexora"></span>
      <span role="img" aria-label="Professional network"></span>
      <span role="img" aria-label="News feed"></span>
    </div>
    <div class="footer-links">
      <div>About Us | Contact Us | Privacy Policy | Terms of Service | Site map</div>
      <div>All rights reserved. © 2011 Tessel Hub.com</div>
    </div>
  </footer>

</div>
</body>
</html>
```